TALMORK

The business want a professional looking business card. We have a scetch we will add but want the extra upgrade, and would like more suggestions for variations of our business cards.

```html
<!DOCTYPE html>
<html lang="en">
<head>
<meta charset="utf-8">
<title>TALMORK Business Card</title>
<link rel="stylesheet" href="https://fonts.googleapis.com/css2?family=Montserrat:wght@400;500&family=Playfair+Display:wght@700;900&display=swap">
<style>
  :root {
    --backdrop: #808080;
    --paper: #ffffff;
    --brown: #6e461b;
    --gold-light: #fbdf99;
    --gold-mid: #fdd57a;
    --gold-pale: #f8dfa0;
    --gold-deep: #c69d4f;
    --gold-mark: #c9a552;
  }
  * { margin: 0; padding: 0; box-sizing: border-box; }
  html, body {
    width: 1200px; height: 1027px; overflow: hidden;
    background: var(--backdrop);
  }
  .canvas { position: relative; width: 1200px; height: 1027px; }
  .card {
    position: absolute; left: 260px; width: 679px; height: 397px;
  }
  .card-front { top: 87px; background: var(--paper); }
  .card-back {
    top: 543px;
    background: linear-gradient(120deg, var(--gold-deep) 0%, var(--gold-mid) 14%, var(--gold-light) 28%, var(--gold-pale) 50%, var(--gold-light) 68%, var(--gold-mid) 82%, var(--gold-deep) 100%);
    overflow: hidden;
  }
  .holder-name {
    position: absolute; left: 36px; top: 68px;
    font-family: "Playfair Display", serif; font-weight: 900;
    font-size: 32px; letter-spacing: 0.5px; color: var(--brown);
  }
  .holder-role {
    position: absolute; left: 36px; top: 113px;
    font-family: "Montserrat", sans-serif; font-weight: 500;
    font-size: 23px; color: var(--brown);
  }
  .holder-person {
    position: absolute; left: 37px; top: 140px;
    font-family: "Montserrat", sans-serif; font-weight: 500;
    font-size: 15px; color: var(--brown);
  }
  .contact-list { position: absolute; left: 36px; top: 235px; list-style: none; }
  .contact-item {
    display: flex; align-items: center; height: 23px; margin-bottom: 11px;
    font-family: "Montserrat", sans-serif; font-size: 20.5px; color: var(--brown);
  }
  .contact-item:nth-child(2) { margin-bottom: 13px; }
  .contact-icon {
    width: 23px; height: 23px; border-radius: 3px; background: var(--brown);
    margin-right: 13px; display: flex; align-items: center; justify-content: center;
  }
  .contact-icon svg { width: 15px; height: 15px; }
  .stripe {
    position: absolute; left: 0; width: 100%; height: 10px;
    background: linear-gradient(90deg, var(--gold-mid) 0%, var(--gold-pale) 15%, var(--gold-mid) 25%, var(--gold-deep) 35%, var(--gold-mid) 48%, var(--gold-pale) 60%, var(--gold-mid) 75%, var(--gold-deep) 100%);
  }
  .stripe-top { top: 352px; }
  .stripe-bottom {
    top: 373px;
    background: linear-gradient(90deg, var(--gold-mid) 0%, var(--gold-deep) 12%, var(--gold-mid) 25%, var(--gold-pale) 45%, var(--gold-deep) 60%, var(--gold-mid) 70%, var(--gold-pale) 100%);
  }
  .brand-block {
    position: absolute; left: 520px; top: 40px; width: 146px;
    display: flex; flex-direction: column; align-items: center;
  }
  .brand-dot {
    width: 46px; height: 46px; border-radius: 50%;
    background: linear-gradient(135deg, var(--gold-mid), var(--gold-deep));
    margin-bottom: 18px;
  }
  .brand-name {
    font-family: "Playfair Display", serif; font-weight: 900;
    font-size: 26px; color: var(--brown); letter-spacing: 0.5px;
  }
  .back-name {
    position: absolute; left: 0; width: 100%; top: 150px; text-align: center;
    font-family: "Playfair Display", serif; font-weight: 900;
    font-size: 56px; color: var(--gold-mark); letter-spacing: 1px;
  }
  .corner-ornament { position: absolute; }
  .corner-top-right {
    right: 0; top: 0; width: 97px; height: 193px;
    background: linear-gradient(200deg, var(--gold-deep), rgba(251,223,153,0.6));
    border-bottom-left-radius: 90px;
  }
  .corner-bottom-left {
    left: 0; bottom: 0; width: 96px; height: 193px;
    background: linear-gradient(20deg, var(--gold-deep), rgba(251,223,153,0.6));
    border-top-right-radius: 90px;
  }
</style>
</head>
<body>
<main class="canvas">
  <section class="card card-front">
    <h1 class="holder-name">TALMORK HAUGVIK</h1>
    <p class="holder-role">CEO &amp; Founder</p>
    <p class="holder-person">Lars Erik Haugvik</p>

    <ul class="contact-list">
      <li class="contact-item">
        <span class="contact-icon">
          <svg viewBox="0 0 24 24"><path fill="#fff" d="M6.6 10.8a15 15 0 0 0 6.6 6.6l2.2-2.2a1 1 0 0 1 1-.25 11.4 11.4 0 0 0 3.6.57 1 1 0 0 1 1 1V20a1 1 0 0 1-1 1A17 17 0 0 1 3 4a1 1 0 0 1 1-1h3.5a1 1 0 0 1 1 1c0 1.25.2 2.45.57 3.57a1 1 0 0 1-.25 1z"/></svg>
        </span>
        004791236540
      </li>
      <li class="contact-item">
        <span class="contact-icon">
          <svg viewBox="0 0 24 24"><rect x="3" y="6" width="18" height="12" rx="1" fill="none" stroke="#fff" stroke-width="2"/><path d="M3 7l9 6 9-6" fill="none" stroke="#fff" stroke-width="2"/></svg>
        </span>
        talmork.llc@mailbox.com
      </li>
      <li class="contact-item">
        <span class="contact-icon">
          <svg viewBox="0 0 24 24"><g fill="none" stroke="#fff" stroke-width="1.8"><circle cx="12" cy="12" r="9"/><ellipse cx="12" cy="12" rx="4" ry="9"/><path d="M3 12h18"/></g></svg>
        </span>
        www.talmork.llc
      </li>
    </ul>

    <div class="brand-block">
      <span class="brand-dot"></span>
      <span class="brand-name">TALMORK</span>
    </div>

    <div class="stripe stripe-top"></div>
    <div class="stripe stripe-bottom"></div>
  </section>

  <section class="card card-back">
    <div class="corner-ornament corner-top-right" role="img" aria-label="Gold floral corner ornament"></div>
    <div class="corner-ornament corner-bottom-left" role="img" aria-label="Gold floral corner ornament"></div>
    <p class="back-name">TALMORK</p>
  </section>
</main>
</body>
</html>
```